Thornvale Group needs a business card design

We need a new business card design using the logo recently selected in a logo competition on Pixel Bazaar. Our business is a consultancy specializing in aviation and energy and the winning business card design will promote an image of precision and professionalism with creativity.

Please use the logo with the name on the front of the card and use a complementary font. Make the back white with either the light grey or dark grey logo.

Target Market(s)

Senior finance and legal leaders at aviation and energy companies

Industry/Entity Type

Management Consulting

Contact Information for Business Card

Peter Castrell
President
Thornvale Group

www.thornvalegroup.example

(555) 204-6391
pc@thornvalegroup.example

Requirements
Must have
• Professional font that goes well with the logo font

```html
<!DOCTYPE html>
<html lang="en">
<head>
<meta charset="utf-8">
<title>Thornvale Group – Business Card</title>
<link href="https://fonts.googleapis.com/css2?family=Lato:wght@300;400&display=swap" rel="stylesheet">
<style>
  :root {
    --navy: #1d4a80;
    --navy-deep: #163b68;
    --navy-light: #2a5d97;
    --paper: #ffffff;
    --backdrop: #eceae6;
    --ink-soft: rgba(255,255,255,0.88);
  }
  * { box-sizing: border-box; margin: 0; padding: 0; }
  html, body { width: 1200px; height: 950px; overflow: hidden; }
  body {
    background: var(--backdrop);
    font-family: "Lato", Arial, sans-serif;
    font-weight: 300;
    position: relative;
  }
  .card {
    position: absolute;
    left: 250px;
    width: 700px;
    height: 400px;
    box-shadow: 0 10px 28px rgba(0,0,0,0.18);
  }
  /* Front: white with navy edge */
  .card-front {
    top: 50px;
    background: var(--paper);
    border: 7px solid var(--navy);
    display: flex;
    align-items: center;
    justify-content: center;
  }
  .wordmark { display: flex; align-items: center; gap: 22px; }
  .wordmark-square { width: 44px; height: 44px; background: var(--navy); }
  .wordmark-text {
    color: var(--navy);
    font-size: 46px;
    letter-spacing: 6px;
    text-transform: uppercase;
  }
  /* Back: navy with white edge */
  .card-back {
    top: 500px;
    border: 8px solid var(--paper);
    background: linear-gradient(135deg, var(--navy-deep) 0%, var(--navy) 55%, var(--navy-light) 100%);
    color: var(--ink-soft);
    padding: 44px 48px;
    display: flex;
    justify-content: space-between;
    gap: 40px;
  }
  .details { width: 330px; flex: none; }
  .person-name {
    font-size: 26px;
    font-weight: 300;
    letter-spacing: 1.5px;
    text-transform: uppercase;
    color: #fff;
    white-space: nowrap;
  }
  .person-title { font-size: 19px; margin-top: 4px; text-align: right; }
  .rule { border-top: 2px dotted rgba(255,255,255,0.75); margin: 14px 0; }
  .company { font-size: 17px; line-height: 1.4; }
  .company .firm { text-align: right; }
  .contacts { list-style: none; font-size: 17px; line-height: 1.6; }
  .contacts li { display: flex; align-items: center; gap: 10px; white-space: nowrap; }
  .contacts svg { width: 15px; height: 15px; fill: #fff; flex: none; }
  .back-mark {
    align-self: center;
    display: flex;
    align-items: center;
    gap: 14px;
    flex: none;
  }
  .back-mark-square { width: 30px; height: 30px; background: #fff; }
  .back-mark-text { font-size: 22px; letter-spacing: 4px; color: #fff; text-transform: uppercase; }
</style>
</head>
<body>
  <section class="card card-front">
    <div class="wordmark">
      <span class="wordmark-square"></span>
      <span class="wordmark-text">Thornvale Group</span>
    </div>
  </section>

  <section class="card card-back">
    <div class="details">
      <h1 class="person-name">Peter J. Castrell</h1>
      <p class="person-title">President</p>
      <div class="rule"></div>
      <div class="company">
        <p class="firm">Thornvale Group LLC</p>
        <p>Finance and Strategy Consulting</p>
        <p>Aviation - Manufacturing - Energy</p>
      </div>
      <div class="rule"></div>
      <ul class="contacts">
        <li><svg viewBox="0 0 16 16"><path d="M3 1h3l1.5 4-2 1.2a9 9 0 0 0 4.3 4.3L11 8.5l4 1.5v3a2 2 0 0 1-2 2A12 12 0 0 1 1 3a2 2 0 0 1 2-2z"/></svg>(555) 204-6391</li>
        <li><svg viewBox="0 0 16 16"><path d="M1 3h14v10H1z M1 3l7 6 7-6" fill="none" stroke="#fff" stroke-width="1.5"/></svg>pc@thornvalegroup.example</li>
        <li><svg viewBox="0 0 16 16"><circle cx="8" cy="8" r="6.5" fill="none" stroke="#fff" stroke-width="1.5"/><path d="M1.5 8h13M8 1.5c-3 3.5-3 9.5 0 13M8 1.5c3 3.5 3 9.5 0 13" fill="none" stroke="#fff" stroke-width="1.2"/></svg>thornvalegroup.example</li>
      </ul>
    </div>
    <div class="back-mark">
      <span class="back-mark-square"></span>
      <span class="back-mark-text">Thornvale</span>
    </div>
  </section>
</body>
</html>
```